Visitenkarten für Urologisches Zentrum
Zielgruppe
Urologisches Zentrum Lindenhof / Vasektomie-Zentrum Lindenhof
Aufgabenstellung
Bitte an der alten Vorlage orientieren. Die 1. Seite (Aussenseite der Klappkarte) ist in Ordnung.
2. Seite (Innenseite der Klappkarte): Hier ggf. eine besser lesbare Schrift.
Adresse: Dr. med. Felix Brandt &
Dr. med. Martin Sommer
Eibenweg 7
68161 Mannheim
Fon: unverändert, jedoch bitte etwas übersichtlicher
Fax: unverändert, jedoch bitte etwas übersichtlicher
E-Mail: unverändert, jedoch bitte etwas übersichtlicher
Web: unverändert, jedoch bitte etwas übersichtlicher
Öffnungszeiten: Mo,Di: 08:00 - 12:00 Uhr
14:00 - 16:00 Uhr
Mi: 08:00 - 12:00 Uhr
Do,Fr: 08.00 - 12:00 Uhr
Es sollte noch folgender Text eingefügt werden: Wußten Sie schon? Sie können bei uns Termine über www.terminvorbei.de
vereinbaren.
Bitte machen Sie uns einige dynamischere Gestaltungsvorschläge. Die Karte sollte in weiß gehalten werden. Keine Glanzbeschichtung und etwas kräftigeres, hochwertiges Papier.
Ich freue mich auf Ihre Vorschläge.

```html
<!DOCTYPE html>
<html lang="de">
<head>
<meta charset="utf-8">
<title>Visitenkarte Innenseite – Urologisches Zentrum Lindenhof</title>
<link rel="stylesheet" href="https://fonts.googleapis.com/css2?family=Ubuntu:wght@300;400;700&display=swap">
<style>
  :root {
    --paper: #ffffff;
    --ink: #111111;
    --accent: #86b027;
    --fold: #9a9a9a;
  }
  html, body {
    margin: 0;
    padding: 0;
    overflow: hidden;
    background: var(--paper);
  }
  .card {
    position: relative;
    width: 1200px;
    height: 388px;
    background: var(--paper);
    font-family: "Ubuntu", sans-serif;
    color: var(--ink);
    overflow: hidden;
  }
  .fold-line {
    position: absolute;
    left: 601px;
    top: 0;
    width: 1px;
    height: 388px;
    background: var(--fold);
  }
  .vertical-title {
    position: absolute;
    writing-mode: vertical-rl;
    transform: rotate(180deg);
    color: var(--accent);
    font-weight: 700;
    white-space: nowrap;
    margin: 0;
  }
  .doctors {
    left: 86px;
    top: 66px;
    height: 256px;
    font-size: 21.5px;
    line-height: 20px;
    letter-spacing: 0.1px;
  }
  .hours-title {
    left: 705px;
    top: 108px;
    height: 170px;
    font-size: 23px;
    line-height: 24px;
  }
  .contact {
    position: absolute;
    left: 161px;
    top: 60px;
    margin: 0;
    font-style: normal;
    font-weight: 300;
    font-size: 33px;
    line-height: 39px;
  }
  .contact .label {
    font-size: 17px;
    font-weight: 300;
    margin-left: 4px;
  }
  .hours {
    position: absolute;
    left: 764px;
    top: 79px;
    margin: 0;
    font-weight: 300;
    font-size: 33px;
    line-height: 39px;
  }
  .hours p { margin: 0; }
  .hours p + p { margin-top: 39px; }
  .booking-note {
    position: absolute;
    left: 763px;
    top: 331px;
    margin: 0;
    font-size: 11.2px;
    line-height: 13px;
    letter-spacing: -0.2px;
    font-weight: 400;
  }
  .booking-note .link { color: var(--accent); }
</style>
</head>
<body>
  <main class="card">
    <h1 class="vertical-title doctors">Dr. med. Felix Brandt &amp;<br>Dr. med. Martin Sommer</h1>
    <address class="contact">
      Eibenweg 7<br>
      68161 Mannheim<br>
      0621 174 38<br>
      0621 582 093 10<br>
      0621 174 38<span class="label">Fax</span><br>
      praxis@brandt-sommer.de<br>
      www.brandt-sommer.de
    </address>

    <div class="fold-line"></div>

    <h2 class="vertical-title hours-title">Öffnungszeiten</h2>
    <div class="hours">
      <p>Montag bis Freitag<br>08:00 - 12:00</p>
      <p>Montag, Dienstag,<br>Donnerstag, Freitag<br>14:00 - 16:00</p>
    </div>
    <p class="booking-note">Wußten Sie schon? Sie können bei uns Termine<br>über <span class="link">www.terminvorbei.de</span> vereinbaren.</p>
  </main>
</body>
</html>
```